Zolvana Stationary and Branding Documents

Corporate Identity Branding stationary needed for IT Recruiting Firm.

I already have a Logo, business cards and website. I need to get designs completed for the remaining corporate identity documents.

The documentation should use similar colors as my website and business card. The designs should modern and clean.

http://zolvanaworks.example/

Target Market(s)

Information Technology Industry

Industry/Entity Type

Information Technology

Colors
3377b5
0255a3
fbee3e
f78f20
f37122
33a6d7
000000
0592cd

Requirements
Must have
• Letter Head
• Folder Design
• PowerPoint Design
• Invoice
• Envelope
Nice to have
• Proposal
• Flyer
• Brochure
Should not have
• Logo
• Business Cards
• Website

```html
<!DOCTYPE html>
<html lang="en">
<head>
<meta charset="utf-8">
<title>Zolvana Stationery Set</title>
<link rel="stylesheet" href="https://fonts.googleapis.com/css2?family=Ubuntu:wght@400;500&family=Open+Sans:wght@400;600;700&family=Didact+Gothic&family=Cinzel:wght@400&display=swap">
<style>
  :root{
    --blue:#0255a3;
    --blue-mid:#3377b5;
    --blue-light:#1a73c0;
    --orange:#f37122;
    --orange-warm:#f78f20;
    --dark:#2f2f31;
    --grey-row:#e6e6e6;
    --grey-text:#6d6d6d;
    --page:#ffffff;
    --bg:#f1f2f4;
  }
  *{box-sizing:border-box;margin:0;padding:0}
  html,body{width:1200px;height:1200px;overflow:hidden;background:var(--bg)}
  body{position:relative;font-family:"Open Sans",sans-serif}

  .sheet{position:absolute;background:var(--page);overflow:hidden}
  .swoosh{position:absolute;left:0;bottom:0;width:100%;display:block}

  .wordmark{font-family:"Ubuntu",sans-serif;font-weight:500;color:var(--blue);line-height:1;letter-spacing:.5px;white-space:nowrap}
  .tagline{font-family:"Ubuntu",sans-serif;color:var(--orange);letter-spacing:.8px;line-height:1;white-space:nowrap}

  /* Letterhead */
  .letterhead{left:76px;top:42px;width:381px;height:538px}
  .letterhead .wordmark{position:absolute;left:27px;top:24px;font-size:27px}
  .letterhead .tagline{position:absolute;left:32px;top:53px;font-size:6.5px}
  .letterhead .rule{position:absolute;left:139px;top:53px;width:202px;border-top:1px solid var(--blue-mid)}
  .letterhead .address{position:absolute;right:40px;top:45px;font-size:4.5px;font-weight:700;color:var(--orange)}
  .letterhead .contact{position:absolute;right:40px;top:56px;font-size:4.5px;color:var(--grey-text)}
  .letterhead .site{position:absolute;right:12px;bottom:10px;font-size:6px;font-weight:700;color:#fff}

  /* Invoice */
  .invoice{left:498px;top:38px;width:416px;height:538px;font-family:"Didact Gothic",sans-serif;color:var(--grey-text)}
  .invoice .brand{position:absolute;right:39px;top:39px;text-align:center}
  .invoice .brand .wordmark{font-size:29px}
  .invoice .brand .tagline{font-size:7px;margin-top:2px}
  .invoice-title{position:absolute;left:38px;top:90px;font-size:15px;font-weight:400;color:var(--orange)}
  .invoice-title b{font-weight:400;font-size:20px}
  .invoice-dates{position:absolute;left:38px;top:113px;font-size:6px;line-height:9px}
  .parties{position:absolute;left:38px;top:133px;width:339px;height:76px;border:1px solid var(--orange);display:flex;gap:3px;padding:2px}
  .party{flex:1;display:flex;flex-direction:column}
  .party-head{background:var(--blue);color:#fff;font-size:7px;height:19px;line-height:19px;padding-left:6px;border-radius:2px}
  .party-body{display:flex;gap:3px;margin-top:3px;flex:1}
  .party-mark{width:42px;height:40px;display:flex;align-items:center;justify-content:center;font-family:"Ubuntu",sans-serif;font-weight:500;font-size:8px;color:var(--blue);border:1px solid #eee}
  .party-mark.empty{color:#ddd;font-family:"Didact Gothic",sans-serif;font-weight:400}
  .party-lines{flex:1;list-style:none}
  .party-lines li{background:var(--grey-row);font-size:4.5px;height:8px;line-height:8px;margin-bottom:1.6px;padding-left:3px}
  .items-label{position:absolute;left:41px;top:217px;font-size:7px}
  .items{position:absolute;left:40px;top:228px;width:337px;border-collapse:separate;border-spacing:0 2px;font-size:5px;border:1px solid #eee}
  .items th{background:var(--orange);color:#fff;font-weight:400;height:19px;text-align:left;padding-left:9px}
  .items th.num,.items td.num{text-align:center;padding-left:0}
  .items td{background:var(--grey-row);height:19px;padding-left:4px;border-right:2px solid #fff}
  .items tr td:last-child,.items tr th:last-child{border-right:none}
  .notes{position:absolute;left:38px;top:410px;width:218px;height:66px;border:1px solid #e6e6e6;padding:9px 6px;font-size:5.5px}
  .notes i{display:block;border-bottom:1px solid #eee;height:9px}
  .footnote{position:absolute;left:42px;top:482px;font-size:4px}
  .amount{position:absolute;left:271px;top:404px;width:105px;font-size:5px;text-align:right}
  .amount-head{background:var(--blue);color:#fff;text-align:center;font-size:8px;height:19px;line-height:19px;margin-bottom:2px}
  .amount-row{display:flex;height:17px;line-height:17px;border-bottom:1px solid #eee}
  .amount-row span:first-child{width:35px;padding-right:2px;border-right:1px solid #eee}
  .amount-row span:last-child{flex:1;padding-right:14px}
  .amount-total{display:flex;height:20px;line-height:20px;justify-content:flex-end;gap:3px;padding-right:6px}
  .amount-total b{font-weight:400;font-size:11px}

  /* Folder */
  .folder{left:72px;top:594px;width:434px;height:578px;background:linear-gradient(180deg,var(--blue-light) 0%,var(--blue) 70%);border-top:3px solid var(--orange)}
  .folder .brand{position:absolute;left:0;right:0;top:80px;text-align:center}
  .folder .wordmark{color:#fff;font-size:72px;letter-spacing:1px}
  .folder .tagline{font-size:17px;margin-top:8px;color:var(--orange-warm)}
  .folder .photo-wave{position:absolute;left:0;top:0;width:100%;height:100%}
  .folder .band{position:absolute;left:0;bottom:0;width:100%;height:36px;background:linear-gradient(180deg,var(--orange-warm),var(--orange));color:#fff;font-family:"Cinzel",serif;font-size:15px;letter-spacing:1px;text-align:center;line-height:36px}

  /* Envelope front */
  .envelope{left:550px;top:601px;width:582px;height:293px}
  .envelope .wordmark{position:absolute;left:21px;top:18px;font-size:37px}
  .envelope .tagline{position:absolute;left:27px;top:56px;font-size:10px;padding:0 4px 3px 4px;border-bottom:1px solid var(--blue-mid)}
  .envelope .address{position:absolute;left:38px;top:74px;font-size:6.5px;line-height:1;font-weight:700;color:var(--orange);white-space:nowrap}
  .envelope .contact{position:absolute;left:32px;top:86px;font-size:6.5px;line-height:1;color:var(--grey-text);white-space:nowrap}
  .envelope .site{position:absolute;right:25px;bottom:14px;font-size:8px;font-weight:700;color:#fff}

  /* Envelope back */
  .envelope-back{left:551px;top:910px;width:587px;height:274px;background:var(--blue)}
  .envelope-back svg{position:absolute;inset:0;width:100%;height:100%}
</style>
</head>
<body>

<section class="sheet letterhead">
  <div class="wordmark">zolvana</div>
  <div class="tagline">- BUSINESS SOLUTION LLC -</div>
  <div class="rule"></div>
  <div class="address">Four Harbor Plaza 210, 9th Avenue</div>
  <div class="contact">&#9742; 5550102468 &nbsp;&#9993; info@zolvanaworks.example</div>
  <svg class="swoosh" viewBox="0 0 381 56" height="56" preserveAspectRatio="none">
    <polygon points="0,10 240,30 240,56 0,56" fill="var(--dark)"/>
    <polygon points="170,27 260,29 250,31 180,30" fill="var(--orange)"/>
    <polygon points="30,56 381,0 381,56" fill="var(--blue)"/>
  </svg>
  <div class="site">www.zolvanaworks.example</div>
</section>

<section class="sheet invoice">
  <div class="brand">
    <div class="wordmark">zolvana</div>
    <div class="tagline">- BUSINESS SOLUTION LLC -</div>
  </div>
  <h1 class="invoice-title">Invoice <b>0001</b></h1>
  <p class="invoice-dates">01 September , 2012<br>Payment due by 25 November 2012</p>

  <div class="parties">
    <div class="party">
      <div class="party-head">FROM</div>
      <div class="party-body">
        <div class="party-mark">zolvana</div>
        <ul class="party-lines"><li>Your Address</li><li>Address Line 1</li><li>Town</li><li>Region/State</li><li>Zip/Postal Code</li></ul>
      </div>
    </div>
    <div class="party">
      <div class="party-head">TO</div>
      <div class="party-body">
        <div class="party-mark empty">LOGO</div>
        <ul class="party-lines"><li>Your Address</li><li>Address Line 1</li><li>Town</li><li>Region/State</li><li>Zip/Postal Code</li></ul>
      </div>
    </div>
  </div>

  <div class="items-label">ITEMS</div>
  <table class="items">
    <thead><tr><th style="width:36px">Quantity</th><th>Description</th><th class="num" style="width:50px">Unit Price</th><th class="num" style="width:50px">TOTAL</th></tr></thead>
    <tbody>
      <tr><td class="num">2</td><td>Donec ac erat vel neque molestie convallis.</td><td class="num">$600</td><td class="num">$1200</td></tr>
      <tr><td class="num">1</td><td>Sed eget risus ac lacus tempus sollicitudin in at magna.</td><td class="num">$300</td><td class="num">$300</td></tr>
      <tr><td class="num">3</td><td>Nunc auctor nisl vel lorem aliquet pellentesque.</td><td class="num">$800</td><td class="num">$2400</td></tr>
      <tr><td class="num">2</td><td>Pellentesque habitant morbi.</td><td class="num">$20</td><td class="num">$40</td></tr>
      <tr><td class="num">2</td><td>In hac habitasse platea dictumst mauris at.</td><td class="num">$2500</td><td class="num">$5000</td></tr>
      <tr><td class="num">1</td><td>&nbsp;Aenean eget enim eget augue dictum fringilla et vitae.</td><td class="num">$100</td><td class="num">$100</td></tr>
    </tbody>
  </table>

  <div class="notes">Special Notes<i></i><i></i><i></i></div>
  <div class="footnote">molestie condimentum. Curabitur mi dui, faucibus sed</div>

  <div class="amount">
    <div class="amount-head">AMOUNT DUE</div>
    <div class="amount-row"><span>SUBTOTAL</span><span>$9,040</span></div>
    <div class="amount-row"><span>TAX</span><span>$00.00</span></div>
    <div class="amount-row"><span>SHIPPING</span><span>$00.00</span></div>
    <div class="amount-total"><span>TOTAL</span><b>$9,040.00</b></div>
  </div>

  <svg class="swoosh" viewBox="0 0 416 50" height="50" preserveAspectRatio="none">
    <polygon points="0,12 260,30 260,50 0,50" fill="var(--dark)"/>
    <polygon points="180,27 290,30 280,32 190,30" fill="var(--orange)"/>
    <polygon points="80,50 416,0 416,50" fill="var(--blue)"/>
  </svg>
</section>

<section class="sheet folder">
  <div class="brand">
    <div class="wordmark">zolvana</div>
    <div class="tagline">- BUSINESS SOLUTION LLC -</div>
  </div>
  <svg class="photo-wave" viewBox="0 0 434 575" preserveAspectRatio="none">
    <defs>
      <linearGradient id="photoTone" x1="0" y1="0" x2="1" y2="1">
        <stop offset="0" stop-color="#9fc3df"/>
        <stop offset=".5" stop-color="#c9d6e0"/>
        <stop offset="1" stop-color="#3b4f6a"/>
      </linearGradient>
    </defs>
    <path d="M0,545 C40,430 120,400 250,360 C360,325 420,290 434,230 L434,545 Z" fill="#dfe6ee"/>
    <path role="img" aria-label="Photo of three business colleagues smiling around a meeting table in a bright office" d="M0,545 C45,440 125,412 255,372 C365,338 425,300 434,250 L434,545 Z" fill="url(#photoTone)"/>
  </svg>
  <div class="band">JOIN THE ELITE</div>
</section>

<section class="sheet envelope">
  <div class="wordmark">zolvana</div>
  <div class="tagline">- BUSINESS SOLUTION LLC -</div>
  <div class="address">Four Harbor Plaza 210, 9th Avenue</div>
  <div class="contact">&#9742; 5550102468 &#9993; info@zolvanaworks.example</div>
  <svg class="swoosh" viewBox="0 0 582 76" height="76" preserveAspectRatio="none">
    <polygon points="0,2 360,40 360,76 0,76" fill="var(--dark)"/>
    <polygon points="250,36 370,40 360,42 260,39" fill="var(--orange)"/>
    <polygon points="90,76 582,0 582,76" fill="var(--blue)"/>
  </svg>
  <div class="site">www.zolvanaworks.example</div>
</section>

<section class="sheet envelope-back">
  <svg viewBox="0 0 587 274" preserveAspectRatio="none">
    <path d="M8,8 L40,136 Q44,150 60,150 L527,150 Q543,150 547,136 L579,8" fill="none" stroke="#014a8f" stroke-width="2"/>
    <path d="M8,266 L110,160 M579,266 L477,160" stroke="#014a8f" stroke-width="2" fill="none"/>
  </svg>
</section>

</body>
</html>
```